Coffee House With Cycling Theme Wants Business Cards

We want to create a business card for a coffee house that has a cycling theme. We expect to use the current logo on one side of the business card and we have been considering adding the words 'COFFEE HOUSE' underneath (see example). For the other side of the business card we want an interesting design with tag-line, address and social media links (the normal business card stuff). See examples provided but we are not fixed on having it exactly as shown, we are very open to great creative ideas. Please note our logo has the initials ‘KR' in orange embedded in the design and this must be retained. However, you can play with the words COFFEE HOUSE as well as use the orange color on the backside of the business card, as you see fit. For an image on the backside of the business card it can be a photo, hand-drawn or whatever but it must visually combine coffee and cycling in some way. The interior of the Coffee House will be reclaimed wood, rustic and have an urban feel to it with cycling artifacts hanging from the walls/ceiling, etc. Finally, it would be beneficial if the business card design elements can be easily used on flyers and other promotional assets. Good luck, we are looking forward to seeing your creative ideas.

Target Market(s)

Coffee lovers and cycling fans

Contact Information for Business Card

See project description.

Colors

Designer to choose colors to be used in the design.

Requirements
Must have
• Must use the current logo provided and combine a coffee and bike theme.
Nice to have
• Orange is used in current logo and could be used as an accent color on the backside of the business card.

```html
<!DOCTYPE html>
<html lang="en">
<head>
<meta charset="utf-8">
<title>KR Coffee House – Business Cards</title>
<link href="https://fonts.googleapis.com/css2?family=Montserrat:wght@300;400;700&display=swap" rel="stylesheet">
<style>
  :root {
    --bg: #1f1f1f;
    --orange: #f0662a;
    --white: #ffffff;
    --espresso: #3a2214;
    --roast: #6b4026;
    --crema: #a8775a;
    --veil: rgba(255, 255, 255, 0.32);
  }
  * { margin: 0; padding: 0; box-sizing: border-box; }
  html, body {
    width: 1200px; height: 960px; overflow: hidden;
    background: var(--bg);
    font-family: "Montserrat", Arial, sans-serif;
  }
  .stage { position: relative; width: 1200px; height: 960px; }

  .card {
    position: absolute;
    width: 560px; height: 320px;
    box-shadow: 0 18px 40px rgba(0,0,0,0.55);
    overflow: hidden;
  }

  /* Front */
  .card-front {
    left: 100px; top: 110px;
    background: var(--orange);
    display: flex; align-items: center; justify-content: center;
  }
  .brand-name {
    font-weight: 700; line-height: 1; letter-spacing: 4px;
  }
  .card-front .brand-name { font-size: 110px; color: var(--white); }

  /* Back */
  .card-back {
    left: 540px; top: 500px;
    background: var(--espresso);
  }
  .card-back .photo {
    position: absolute; inset: 0;
    background: linear-gradient(135deg, var(--crema) 0%, var(--roast) 50%, var(--espresso) 100%);
  }
  .card-back .veil {
    position: absolute; left: 26px; top: 18px; right: 26px; bottom: 22px;
    background: var(--veil);
  }
  .card-back .brand-name {
    position: absolute; left: 80px; top: 138px;
    font-size: 68px; color: var(--orange); letter-spacing: 3px;
  }

  .contact {
    position: absolute; left: 300px; top: 46px;
    color: var(--white);
  }
  .contact .name { font-weight: 700; font-size: 22px; letter-spacing: 0.5px; }
  .contact .title { font-weight: 300; font-size: 13px; margin: 2px 0 14px; }
  .contact ul { list-style: none; }
  .contact li {
    display: flex; align-items: flex-start; gap: 9px;
    font-size: 12.5px; line-height: 1.35; margin-bottom: 9px;
  }
  .contact svg { flex: none; width: 14px; height: 14px; margin-top: 1px; fill: var(--white); }
</style>
</head>
<body>
<main class="stage">
  <section class="card card-front" aria-label="Card front">
    <span class="brand-name">KR</span>
  </section>

  <section class="card card-back" aria-label="Card back">
    <div class="photo" role="img" aria-label="Photo of ground coffee, coffee beans on a wooden table and a cup of coffee"></div>
    <div class="veil"></div>
    <span class="brand-name">KR</span>
    <div class="contact">
      <p class="name">Your Name</p>
      <p class="title">Your Title</p>
      <ul>
        <li>
          <svg viewBox="0 0 24 24" aria-hidden="true"><path d="M6.6 10.8a15 15 0 0 0 6.6 6.6l2.2-2.2c.3-.3.7-.4 1-.2 1.1.4 2.3.6 3.6.6.6 0 1 .4 1 1V20c0 .6-.4 1-1 1A17 17 0 0 1 3 4c0-.6.4-1 1-1h3.5c.6 0 1 .4 1 1 0 1.3.2 2.5.6 3.6.1.3 0 .7-.2 1z"/></svg>
          <span>123-456-2100</span>
        </li>
        <li>
          <svg viewBox="0 0 24 24" aria-hidden="true"><path d="M2 5h20v14H2zm2 2v.4l8 5 8-5V7zm0 2.8V17h16V9.8l-8 5z"/></svg>
          <span>youremail@mailbox.com</span>
        </li>
        <li>
          <svg viewBox="0 0 24 24" aria-hidden="true"><path d="M12 2a10 10 0 1 0 0 20 10 10 0 0 0 0-20zm0 2c1 0 2.3 2 2.8 5H9.2C9.7 6 11 4 12 4zm-7.7 7h3c-.1 1-.1 2 0 3h-3a8 8 0 0 1 0-3zm1 5h2.4c.3 1.3.8 2.5 1.4 3.4A8 8 0 0 1 5.3 16zm3.9-2a14 14 0 0 1 0-3h5.6a14 14 0 0 1 0 3zm2.8 6c-1 0-2.3-2-2.8-4h5.6c-.5 2-1.8 4-2.8 4zm3-.6c.6-.9 1.1-2.1 1.4-3.4h2.4a8 8 0 0 1-3.8 3.4zM16.7 14c.1-1 .1-2 0-3h3a8 8 0 0 1 0 3zm-.4-5c-.3-1.3-.8-2.5-1.4-3.4A8 8 0 0 1 18.7 9zM9.1 5.6C8.5 6.5 8 7.7 7.7 9H5.3a8 8 0 0 1 3.8-3.4z"/></svg>
          <span>www.yourwebsite.com</span>
        </li>
        <li>
          <svg viewBox="0 0 24 24" aria-hidden="true"><path d="M12 2a7 7 0 0 0-7 7c0 5 7 13 7 13s7-8 7-13a7 7 0 0 0-7-7zm0 9.5a2.5 2.5 0 1 1 0-5 2.5 2.5 0 0 1 0 5z"/></svg>
          <span>Your address, city<br>state, ZIP 0000</span>
        </li>
      </ul>
    </div>
  </section>
</main>
</body>
</html>
```